Cloud-based vaccination website

Basic website design for cloud-based medical company

Coding

Coded - Design and coding required

Number of Pages Required

1 page

Colors
3277b5

```html
<!DOCTYPE html>
<html lang="en">
<head>
<meta charset="utf-8">
<title>NUBICA – Cloud Based Medical</title>
<link href="https://fonts.googleapis.com/css2?family=Jost:wght@400;500;600;700;800&family=Open+Sans:wght@400;600&display=swap" rel="stylesheet">
<style>
:root{
  --navy:#0b1a4a;
  --navy-deep:#081440;
  --cyan:#18b4d4;
  --cyan-bright:#1ec4e6;
  --brand:#3277b5;
  --text:#333a4a;
  --white:#ffffff;
  --line:#0b1a4a;
}
*{margin:0;padding:0;box-sizing:border-box}
html,body{width:1200px;height:3184px;overflow:hidden;background:var(--white)}
body{position:relative;font-family:"Jost",sans-serif;color:var(--text)}
.abs{position:absolute}

/* header */
.site-header{position:absolute;left:0;top:0;width:1200px;height:105px;background:var(--white)}
.brand{position:absolute;left:143px;top:48px;display:flex;align-items:center;gap:8px}
.brand-dot{width:22px;height:22px;border-radius:50%;background:var(--brand)}
.brand-name{font-size:34px;font-weight:600;color:var(--navy);letter-spacing:.5px;line-height:1}
.header-mail{position:absolute;right:144px;top:20px;display:flex;align-items:center;gap:10px;font-size:27px;color:var(--navy)}
.main-nav{position:absolute;right:144px;top:72px;display:flex;gap:48px;font-size:16px;font-weight:500;color:var(--navy)}
.main-nav .is-active{color:var(--brand)}

/* hero */
.hero{position:absolute;left:0;top:105px;width:1200px;height:590px}
.hero-photo{position:absolute;inset:0;background:radial-gradient(circle at 50% 32%,#b8ecff 0,#5fbfe6 12%,#8aa6bd 34%,#7d8c9c 70%,#6f7c89 100%)}
.hero-title{position:absolute;left:0;width:1200px;top:48px;text-align:center;font-size:50px;font-weight:800;color:var(--navy);letter-spacing:1px}
.hero-arrow{position:absolute;top:235px;width:40px;height:40px;border-radius:50%;background:var(--navy);display:flex;align-items:center;justify-content:center}

/* section titles */
.section-title{font-size:42px;font-weight:800;color:var(--navy);letter-spacing:.5px;line-height:1}

/* welcome */
.welcome-title{position:absolute;left:143px;top:768px}
.welcome-text{position:absolute;left:143px;top:824px;width:430px;font-size:18px;line-height:35.3px;color:var(--text)}
.btn{display:inline-flex;align-items:center;justify-content:center;font-family:"Jost",sans-serif;font-weight:500;color:var(--white);text-transform:uppercase}
.btn-cyan{background:var(--cyan-bright)}
.btn-navy{background:var(--navy)}
.welcome-btn{position:absolute;left:143px;top:1054px;width:121px;height:39px;font-size:16px}
.welcome-cloud{position:absolute;left:628px;top:796px}

/* services */
.services{position:absolute;left:0;top:1170px;width:1200px;height:660px}
.services-title{position:absolute;left:0;width:1200px;top:1310px;text-align:center;color:var(--white)}
.service-card{position:absolute;top:1368px;width:297px;height:306px;background:var(--white);text-align:center}
.service-icon{position:absolute;left:108px;top:26px}
.service-name{position:absolute;left:0;width:100%;top:127px;font-size:24px;font-weight:500;color:var(--navy)}
.service-text{position:absolute;left:14px;width:269px;top:167px;font-family:"Open Sans",sans-serif;font-size:11.5px;line-height:21px;color:#444}
.service-card .btn{position:absolute;left:88px;top:240px;width:120px;height:40px;font-size:16px}

/* resources */
.resources-title{position:absolute;left:0;width:1200px;top:1905px;text-align:center}
.resource-panel{position:absolute;left:143px;top:1963px;width:913px;height:368px}
.resource-photo{position:absolute;left:0;top:0;width:577px;height:368px;background:linear-gradient(90deg,#3d4854 0%,#1e2a36 45%,#0c1626 100%)}
.resource-body{position:absolute;left:577px;top:0;width:336px;height:368px;background:var(--cyan)}
.resource-pointer{position:absolute;left:-32px;top:166px}
.resource-heading{position:absolute;right:28px;top:32px;text-align:right;font-size:32px;font-weight:500;line-height:40px;color:var(--white)}
.resource-text{position:absolute;right:28px;top:170px;width:290px;text-align:right;font-family:"Open Sans",sans-serif;font-size:13px;line-height:24px;color:var(--white)}
.resource-body .btn{position:absolute;right:28px;top:289px;width:119px;height:39px;font-size:16px}
.chev{position:absolute;top:2132px}

/* contact */
.contact-bg{position:absolute;left:0;top:2400px;width:1200px;height:660px}
.contact-title{position:absolute;left:143px;top:2544px}
.field{position:absolute;background:var(--white);border:1px solid #2a3550;font-family:"Open Sans",sans-serif;font-size:11px;color:#222;padding:14px 0 0 14px}
.submit{position:absolute;left:143px;top:2856px;width:88px;height:39px;font-size:16px}

/* footer */
.site-footer{position:absolute;left:0;top:2980px;width:1200px;height:204px}
.footer-links{position:absolute;left:145px;top:3083px;font-family:"Open Sans",sans-serif;font-size:11.5px;color:#b9c3e0;word-spacing:2px}
.footer-copy{position:absolute;left:145px;top:3123px;font-family:"Open Sans",sans-serif;font-size:11.5px;color:#b9c3e0}
.social{position:absolute;top:3100px;width:22px;height:22px;border-radius:50%;background:#5b6c9a}
</style>
</head>
<body>

<header class="site-header">
  <div class="brand"><span class="brand-dot"></span><span class="brand-name">NUBICA</span></div>
  <div class="header-mail">
    <svg width="26" height="19" viewBox="0 0 26 19"><rect x="0" y="0" width="26" height="19" rx="2" fill="#0b1a4a"/><path d="M2 3 L13 11 L24 3" stroke="#fff" stroke-width="2" fill="none"/></svg>
    <span>info@nubica-health.com</span>
  </div>
  <nav class="main-nav">
    <span class="is-active">HOME</span><span>ABOUT US</span><span>SERVICES</span><span>RESOURCES</span><span>CONTACT US</span>
  </nav>
</header>

<section class="hero">
  <div class="hero-photo" role="img" aria-label="Top view of a person working on a laptop at a desk with a glowing cloud and network lines above"></div>
  <h1 class="hero-title">CLOUD BASED MEDICAL</h1>
  <div class="hero-arrow" style="left:50px"><svg width="14" height="16" viewBox="0 0 14 16"><path d="M10 2 L4 8 L10 14" stroke="#fff" stroke-width="3" fill="none"/></svg></div>
  <div class="hero-arrow" style="left:1106px"><svg width="14" height="16" viewBox="0 0 14 16"><path d="M4 2 L10 8 L4 14" stroke="#fff" stroke-width="3" fill="none"/></svg></div>
  <svg class="abs" style="left:0;top:500px" width="1200" height="90" viewBox="0 0 1200 90">
    <polygon points="0,9 1200,83 1200,90 0,90" fill="#fff"/>
    <polygon points="0,9 1200,83 1200,89 0,22" fill="#18b4d4"/>
  </svg>
</section>

<h2 class="section-title welcome-title">WELCOME TO NUBICA</h2>
<p class="welcome-text">Nullam lorem urna, tempus eget mollis et, dapibus ac sem. Suspendisse gravida ornare pulvinar. Vestibulum luctus ex in egestas fringilla. Fusce nec leo ac urna pulvinar auctor. Mauris bibendum fringilla velit. Nulla in lorem at massa pellentesque posuere. Nulla tristique posuere molestie. Aliquam erat volutpat.</p>
<span class="btn btn-cyan welcome-btn">READ MORE</span>
<svg class="welcome-cloud" width="426" height="276" viewBox="0 0 426 276" role="img" aria-label="Doctor holding a tablet with a glowing digital cloud, framed in a cloud shape">
  <defs><radialGradient id="cloudFill" cx="50%" cy="45%" r="65%"><stop offset="0" stop-color="#5fa6cf"/><stop offset=".45" stop-color="#1d4f74"/><stop offset="1" stop-color="#0d2a45"/></radialGradient></defs>
  <path d="M80 276 C30 276 0 245 0 195 C0 140 45 105 95 115 C110 50 160 30 200 45 C230 0 330 -10 370 50 C410 80 426 130 426 190 C426 245 395 276 350 276 Z" fill="url(#cloudFill)"/>
</svg>

<section>
  <svg class="services" viewBox="0 0 1200 660" role="img" aria-label="Dark blue digital network background with glowing particles">
    <defs><linearGradient id="svcBg" x1="0" y1="0" x2="0" y2="1"><stop offset="0" stop-color="#081440"/><stop offset=".55" stop-color="#0b2350"/><stop offset="1" stop-color="#12406e"/></linearGradient></defs>
    <polygon points="0,4 1200,68 1200,658 0,580" fill="url(#svcBg)"/>
    <polygon points="0,578 1200,655 1200,660 0,592" fill="#1ec4e6"/>
  </svg>
  <h2 class="section-title services-title">SERVICES</h2>

  <div class="service-card" style="left:143px">
    <svg class="service-icon" width="82" height="82" viewBox="0 0 82 82" fill="none" stroke="#1ec4e6" stroke-width="2.5">
      <rect x="3" y="10" width="60" height="50"/><path d="M10 50V40M18 50V33M26 50V38"/><path d="M10 18h20M10 24h16"/><path d="M36 30 L48 20 L60 22 L74 6"/><circle cx="74" cy="6" r="4"/><circle cx="58" cy="60" r="14"/><circle cx="58" cy="60" r="6"/>
    </svg>
    <h3 class="service-name">ALIQUAM ERAT</h3>
    <p class="service-text">Pellentesque blandit lacus eget nunc faucibus, et tincidunt eros viverra. Phasellus consequat sagittis nisi suscipit feugiat.</p>
    <span class="btn btn-cyan">READ MORE</span>
  </div>

  <div class="service-card" style="left:451px">
    <svg class="service-icon" width="82" height="82" viewBox="0 0 82 82" fill="none" stroke="#1ec4e6" stroke-width="2.5">
      <path d="M20 50 L56 14 L68 26 L32 62 Z"/><path d="M62 8 L74 20M66 12 L72 6M74 20 L80 14"/><path d="M26 56 L12 70M10 66 L16 72M6 76 L12 70"/><path d="M34 42l4 4M40 36l4 4M46 30l4 4"/>
    </svg>
    <h3 class="service-name">PRAESENT IACULIS</h3>
    <p class="service-text">Pellentesque blandit lacus eget nunc faucibus, et tincidunt eros viverra. Phasellus consequat sagittis nisi suscipit feugiat.</p>
    <span class="btn btn-cyan">READ MORE</span>
  </div>

  <div class="service-card" style="left:759px">
    <svg class="service-icon" width="82" height="82" viewBox="0 0 82 82" fill="none" stroke="#1ec4e6" stroke-width="2.5">
      <path d="M20 30 C8 30 8 14 20 14 C22 4 38 0 44 8 C52 2 66 6 66 16 C76 16 76 30 66 30 Z"/><path d="M41 30V44M12 44H70M12 44V54M41 44V54M70 44V54"/><rect x="2" y="54" width="20" height="22"/><rect x="31" y="54" width="20" height="22"/><rect x="60" y="54" width="20" height="22"/><path d="M2 65h20M31 65h20M60 65h20"/>
    </svg>
    <h3 class="service-name">MAECENAS CONSE</h3>
    <p class="service-text">Pellentesque blandit lacus eget nunc faucibus, et tincidunt eros viverra. Phasellus consequat sagittis nisi suscipit feugiat.</p>
    <span class="btn btn-cyan">READ MORE</span>
  </div>
</section>

<section>
  <h2 class="section-title resources-title">RESOURCES</h2>
  <svg class="chev" style="left:54px" width="20" height="34" viewBox="0 0 20 34"><path d="M17 3 L4 17 L17 31" stroke="#777" stroke-width="3" fill="none"/></svg>
  <svg class="chev" style="left:1124px" width="20" height="34" viewBox="0 0 20 34"><path d="M3 3 L16 17 L3 31" stroke="#777" stroke-width="3" fill="none"/></svg>
  <div class="resource-panel">
    <div class="resource-photo" role="img" aria-label="Engineer with a laptop standing beside server racks in a data centre"></div>
    <div class="resource-body">
      <svg class="resource-pointer" width="33" height="50" viewBox="0 0 33 50"><polygon points="0,25 33,0 33,50" fill="#18b4d4"/></svg>
      <h3 class="resource-heading">PROIN EGET<br>CONGUE NULLA<br>VEL TEMPOR DIAM</h3>
      <p class="resource-text">Vestibulum condimentum, risus ut posuere cursus, velit justo accumsan sem, lobortis aliquet metus dui eu libero. Pellentesque a imperdiet dolor, et auctor est.</p>
      <span class="btn btn-navy">READ MORE</span>
    </div>
  </div>
</section>

<section>
  <svg class="contact-bg" viewBox="0 0 1200 660" role="img" aria-label="Doctor using a tablet with a translucent overlay of medical icons and a DNA strand">
    <defs><linearGradient id="contactBg" x1="0" y1="0" x2="1" y2="0"><stop offset="0" stop-color="#e6f1f5"/><stop offset=".5" stop-color="#a9d1dc"/><stop offset="1" stop-color="#dfe9ef"/></linearGradient></defs>
    <polygon points="0,4 1200,55 1200,660 0,660" fill="url(#contactBg)"/>
  </svg>
  <h2 class="section-title contact-title">CONTACT US</h2>
  <div class="field" style="left:143px;top:2600px;width:218px;height:40px">Name</div>
  <div class="field" style="left:376px;top:2600px;width:217px;height:40px">Email</div>
  <div class="field" style="left:143px;top:2657px;width:218px;height:39px">Phone</div>
  <div class="field" style="left:376px;top:2657px;width:217px;height:39px">Title</div>
  <div class="field" style="left:143px;top:2713px;width:450px;height:126px">Message</div>
  <span class="btn btn-navy submit">SUBMIT</span>
</section>

<footer>
  <svg class="site-footer" viewBox="0 0 1200 204">
    <polygon points="0,0 1200,74 1200,204 0,204" fill="#0b1a4a"/>
    <polygon points="0,0 1200,74 1200,68 0,-10" fill="#1ec4e6"/>
  </svg>
  <div class="footer-links">Home &nbsp;| &nbsp;About Us &nbsp;| &nbsp;Services &nbsp;| &nbsp;Resources &nbsp;| &nbsp;Contact us</div>
  <div class="footer-copy">Copyright © 2021 &nbsp;NUBICA. &nbsp;All rights reserved.</div>
  <span class="social" style="left:978px"></span>
  <span class="social" style="left:1031px"></span>
</footer>

</body>
</html>
```